Designer Instructions – Updated Referral Program Flyer

(Based on the mock-up in “Brief Layout and Instructions.pdf”)

OVERALL STYLE + LAYOUT

Maintain the same general layout, structure, and flow as the mock-up flyer (front and back).

This is an update of an older flyer, not a full redesign — keep the same sections, proportions, and overall visual feel, but with cleaner, more modern design improvements.

The final flyer should look clean, bold, professional, and high-impact, geared toward realtors, property managers, and contractors who refer work.

FRONT SIDE INSTRUCTIONS
1. Header Section

Remove the Rebuild Harbor Crest logo from the top banner.
(Shown on page 1 of the PDF)

2. Main Headline

Keep the same three-line structure:
EARN
UNLIMITED
CASH

Center it, maximize impact, and increase the font size of CASH so all three words match in importance.

Make the headline bold, clean, and the main focal point.

3. Cash Incentive Box

Keep the "$500 minimum OR 10% per referral" box, but upgrade the graphics to look sharper and more modern.

Ensure the wording matches exactly what’s in the mock-up.

4. Premier Partner Program Ribbon

Clean up and modernize the "PREMIER PARTNER PROGRAM" bar while keeping the same position and structure.

Ensure the checkmark badge remains crisp and professional.

5. Supporting Icons Section

Keep the four icons/benefit boxes (Guaranteed Payout, Free Evaluations, Affordable Solutions, Industry Leaders) in the same order.

Update the icons to cleaner, more modern styles — but maintain the same meanings.

Improve alignment and spacing for sharper visual consistency.

6. Remove Icons in Contact Area

At the bottom (“CALL TEXT OR BOOK ONLINE 858-471-6093 BrightlaneRenovate.com”), remove the phone and internet icons, as noted on page 2 of the PDF.

7. Replace All Images

I (Dorian) will provide all updated stock images separately via email.

Replace the flood/water-damage imagery and roof leak with the new images I send.

Keep image placement and proportions the same as the mock-up.

BACK SIDE INSTRUCTIONS
1. Header Image + “REFER / EARN” Section

Maintain the same large split-image layout (“The more you refer, the more you earn”).

Replace all background imagery with the new assets I will send.

Keep the CASH FLOW image section but modernize the type and spacing.

2. “HOW IT WORKS” Section

Preserve the three-column layout:

Refer Flood, Water & Mold Damage

We Take Care of Everything (evaluations/insurance)

Get Paid to Share

Update images, tighten spacing, and use modern iconography.

3. Remove Phone/Internet Icons

Same as the front side — remove small communication icons and keep only the text/number/URL.

4. Bottom Contact Bar

Keep the blue bar, same wording, same layout — just modernize the style if needed for clarity.

5. Replace All Back-Side Images

Again, I will email you the image assets.

Keep the layout EXACT — just update with higher-quality photos and improved design.

TEXT CONTENT (Keep as-is unless spacing adjustments needed)

All text shown in the PDF should remain exactly the same unless spacing or visual balance requires minor adjustments.
Example from page 3:

“REFER FLOOD, MOLD & CONSTRUCTION JOBS”

“We Schedule a Free Estimate. If Approved, You Get Paid.”

“Everybody Benefits From Referrals”

Everything stays, just refreshed and visually improved.

DESIGN GOALS

Flyer should look high-end and trustworthy, not salesy.

Consistent color theme: blues, whites, yellows, same palette as original.

Use bold, modern fonts with strong readability.

Ensure all headlines pop and all benefit boxes are clean, well-aligned, and evenly spaced.

The final result should feel like a premium referral program flyer for a top-tier restoration/remodel company.

FILES I WILL PROVIDE

I will send the designer:

All replacement stock photos

Any updated logos (if needed)

Original high-resolution version of the mock-up (if available)

Any additional icons preferred

Colors
0054AA
0677BA
7BADD7
CADEEF
E8F1F8

Requirements
Must have
• Designer Instructions – Updated Referral Program Flyer (Based on the mock-up in “Brief Layout and Instructions.pdf”) OVERALL STYLE + LAYOUT Maintain the same general layout, structure, and flow as the mock-up flyer (front and back). This is an update of an older flyer, not a full redesign — keep the same sections, proportions, and overall visual feel, but with cleaner, more modern design improvements. The final flyer should look clean, bold, professional, and high-impact, geared toward realtors, property managers, and contractors who refer work. FRONT SIDE INSTRUCTIONS 1. Header Section Remove the Rebuild Harbor Crest logo from the top banner. (Shown on page 1 of the PDF) 2. Main Headline Keep the same three-line structure: EARN UNLIMITED CASH Center it, maximize impact, and increase the font size of CASH so all three words match in importance. Make the headline bold, clean, and the main focal point. 3. Cash Incentive Box Keep the "$500 minimum OR 10% per referral" box, but upgrade the graphics to look sharper and more modern. Ensure the wording matches exactly what’s in the mock-up. 4. Premier Partner Program Ribbon Clean up and modernize the "PREMIER PARTNER PROGRAM" bar while keeping the same position and structure. Ensure the checkmark badge remains crisp and professional. 5. Supporting Icons Section Keep the four icons/benefit boxes (Guaranteed Payout, Free Evaluations, Affordable Solutions, Industry Leaders) in the same order. Update the icons to cleaner, more modern styles — but maintain the same meanings. Improve alignment and spacing for sharper visual consistency. 6. Remove Icons in Contact Area At the bottom (“CALL TEXT OR BOOK ONLINE 858-471-6093 BrightlaneRenovate.com”), remove the phone and internet icons, as noted on page 2 of the PDF. 7. Replace All Images I (Dorian) will provide all updated stock images separately via email. Replace the flood/water-damage imagery and roof leak with the new images I send. Keep image placement and proportions the same as the mock-up. BACK SIDE INSTRUCTIONS 1. Header Image + “REFER / EARN” Section Maintain the same large split-image layout (“The more you refer, the more you earn”). Replace all background imagery with the new assets I will send. Keep the CASH FLOW image section but modernize the type and spacing. 2. “HOW IT WORKS” Section Preserve the three-column layout: Refer Flood, Water & Mold Damage We Take Care of Everything (evaluations/insurance) Get Paid to Share Update images, tighten spacing, and use modern iconography. 3. Remove Phone/Internet Icons Same as the front side — remove small communication icons and keep only the text/number/URL. 4. Bottom Contact Bar Keep the blue bar, same wording, same layout — just modernize the style if needed for clarity. 5. Replace All Back-Side Images Again, I will email you the image assets. Keep the layout EXACT — just update with higher-quality photos and improved design. TEXT CONTENT (Keep as-is unless spacing adjustments needed) All text shown in the PDF should remain exactly the same unless spacing or visual balance requires minor adjustments. Example from page 3: “REFER FLOOD, MOLD & CONSTRUCTION JOBS” “We Schedule a Free Estimate. If Approved, You Get Paid.” “Everybody Benefits From Referrals” Everything stays, just refreshed and visually improved. DESIGN GOALS Flyer should look high-end and trustworthy, not salesy. Consistent color theme: blues, whites, yellows, same palette as original. Use bold, modern fonts with strong readability. Ensure all headlines pop and all benefit boxes are clean, well-aligned, and evenly spaced. The final result should feel like a premium referral program flyer for a top-tier restoration/remodel company. FILES I WILL PROVIDE I will send the designer: All replacement stock photos Any updated logos (if needed) Original high-resolution version of the mock-up (if available) Any additional icons preferred

```html
<!DOCTYPE html>
<html lang="en">
<head>
<meta charset="utf-8">
<title>Refer a Flood – Referral Program</title>
<link rel="stylesheet" href="https://fonts.googleapis.com/css2?family=Archivo+Black&family=Montserrat:wght@500;600;700;800&display=swap">
<style>
  :root {
    --sky-blue: #1a6aa3;
    --deep-navy: #07263d;
    --brand-navy: #1c3a7c;
    --title-blue: #145a96;
    --water-blue: #1f6fc5;
    --water-light: #3d8ddb;
    --sign-yellow: #fbd600;
    --gold-top: #f8ec38;
    --gold-bottom: #f29a3e;
    --card-light: #f4f4f6;
    --card-grey: #c9cbd0;
    --white: #ffffff;
  }
  * { margin: 0; padding: 0; box-sizing: border-box; }
  html, body { width: 1200px; height: 800px; overflow: hidden; background: var(--white); }
  .flyer {
    position: absolute; left: 33px; top: 33px;
    width: 1134px; height: 733px; overflow: hidden;
    background: radial-gradient(ellipse at 50% 40%, var(--water-light), var(--water-blue) 70%);
    font-family: "Montserrat", sans-serif;
  }
  .hero { position: absolute; left: 0; top: 0; width: 1134px; height: 316px; }
  .hero text.slab { font-family: "Archivo Black", sans-serif; }
  .hero text.steps { font-family: "Montserrat", sans-serif; font-weight: 800; }
  .hero text.program-title { font-family: "Montserrat", sans-serif; font-weight: 800; }

  .steps-row { position: absolute; top: 340px; left: 0; width: 100%; height: 311px; }
  .step-card {
    position: absolute; top: 0; width: 322px; height: 311px;
    border: 4px solid var(--brand-navy); border-radius: 26px; overflow: hidden;
    background: linear-gradient(160deg, var(--card-grey), var(--card-light) 45%, #e2e3e7);
    box-shadow: 0 4px 10px rgba(0, 20, 60, .35);
  }
  .step-card:nth-child(1) { left: 61px; }
  .step-card:nth-child(2) { left: 408px; }
  .step-card:nth-child(3) { left: 756px; }
  .step-photo { height: 174px; width: 100%; }
  .photo-pipe { background: linear-gradient(100deg, #3a3a3c 0%, #6b6b6e 30%, #d9d9db 55%, #bdbdc0 100%); }
  .photo-team { background: linear-gradient(180deg, #e8834a 0%, #f3b56a 22%, #3f6fae 45%, #2a64b8 70%, #c7a77d 100%); }
  .photo-sign { background: linear-gradient(180deg, #4d8fd6 0%, #9cc3ea 40%, #e9f1fa 70%, #7ba9dc 100%); }
  .step-text { text-align: center; color: var(--brand-navy); padding-top: 11px; }
  .step-title { font-weight: 800; font-size: 21px; line-height: 22px; letter-spacing: .3px; text-transform: uppercase; }
  .step-body { font-weight: 600; font-size: 18.5px; line-height: 20.5px; margin-top: 1px; }

  .contact-bar { position: absolute; left: 0; bottom: 0; width: 100%; height: 57px; }
  .contact-tab {
    position: absolute; left: 0; top: 0; width: 466px; height: 57px;
    background: var(--brand-navy);
    clip-path: polygon(0 0, 401px 0, 466px 100%, 0 100%);
  }
  .contact-label {
    position: absolute; left: 64px; top: 10px;
    font-size: 33px; line-height: 38px; color: var(--white); letter-spacing: 2.5px; font-weight: 800;
  }
  .contact-label .soft { font-weight: 500; }
  .contact-details {
    position: absolute; left: 449px; top: 10px;
    font-size: 33px; line-height: 38px; color: var(--white); font-weight: 700; letter-spacing: 1.6px;
  }
</style>
</head>
<body>
<main class="flyer">

  <svg class="hero" viewBox="0 0 1134 316" aria-labelledby="hero-title">
    <title id="hero-title">The more you refer, the more you earn – Refer a Flood</title>
    <defs>
      <linearGradient id="gold" x1="0" y1="0" x2="1" y2="1">
        <stop offset="0" stop-color="var(--gold-top)"/>
        <stop offset="1" stop-color="var(--gold-bottom)"/>
      </linearGradient>
      <linearGradient id="stripe" x1="0" y1="0" x2="1" y2="0">
        <stop offset="0" stop-color="#8e9298"/>
        <stop offset=".5" stop-color="#e6e7ea"/>
        <stop offset="1" stop-color="#9a9ea4"/>
      </linearGradient>
      <linearGradient id="money" x1="0" y1="0" x2="1" y2="1">
        <stop offset="0" stop-color="#cfd3d2"/>
        <stop offset=".5" stop-color="#eceeed"/>
        <stop offset="1" stop-color="#b9bebd"/>
      </linearGradient>
    </defs>

    <rect class="sky-panel" width="1134" height="316" fill="var(--sky-blue)"/>
    <polygon class="navy-panel" points="85,28 595,64 650,257 210,257 85,230" fill="var(--deep-navy)"/>
    <polygon class="how-band" points="0,257 650,257 668,316 0,316" fill="var(--sign-yellow)"/>
    <polygon class="cash-photo" role="img" aria-label="Photo of scattered hundred dollar bills" points="577,0 1134,0 1134,316 678,316" fill="url(#money)"/>
    <polygon class="divider-stripe" points="566,0 580,0 680,316 664,316" fill="url(#stripe)"/>

    <text class="slab" x="85" y="56" font-size="36" fill="var(--white)" textLength="384" lengthAdjust="spacingAndGlyphs">THE MORE YOU</text>
    <text class="slab" x="85" y="120" font-size="82" fill="url(#gold)" textLength="384" lengthAdjust="spacingAndGlyphs">REFER</text>
    <text class="slab" x="85" y="151" font-size="36" fill="var(--white)" textLength="384" lengthAdjust="spacingAndGlyphs">THE MORE YOU</text>
    <text class="slab" x="85" y="228" font-size="102" fill="url(#gold)" textLength="384" lengthAdjust="spacingAndGlyphs">EARN</text>

    <text class="steps" x="88" y="304" font-size="49" fill="var(--brand-navy)" textLength="392" lengthAdjust="spacingAndGlyphs">HOW IT WORKS</text>

    <g class="program-title-block" fill="var(--title-blue)" text-anchor="middle">
      <text class="program-title" x="848" y="104" font-size="62" letter-spacing="14">REFER</text>
      <text class="program-title" x="848" y="176" font-size="62">A</text>
      <text class="program-title" x="848" y="248" font-size="62" letter-spacing="14">FLOOD</text>
    </g>
  </svg>

  <section class="steps-row">
    <article class="step-card">
      <div class="step-photo photo-pipe" role="img" aria-label="Photo of a leaking white drain pipe under a sink"></div>
      <div class="step-text">
        <h2 class="step-title">Refer Flood, Water<br>and Mold Damage</h2>
        <p class="step-body">Our Rapid 24/7 Response<br>Team Arrives Fast to<br>Stop the Damage</p>
      </div>
    </article>
    <article class="step-card">
      <div class="step-photo photo-team" role="img" aria-label="Photo of the restoration team standing before a service van at sunset by a bridge"></div>
      <div class="step-text">
        <h2 class="step-title">We Take Care of<br>Everything</h2>
        <p class="step-body">Free Inspection and Estimates<br>Certified Repairs<br>100% Guarantee</p>
      </div>
    </article>
    <article class="step-card">
      <div class="step-photo photo-sign" role="img" aria-label="Photo of a yellow road sign reading Get Paid to Help People against a cloudy sky"></div>
      <div class="step-text">
        <h2 class="step-title">Get Paid to<br>Help People</h2>
        <p class="step-body">You Get Paid and Your Client<br>Gets The Expert Help<br>They Need Fast</p>
      </div>
    </article>
  </section>

  <footer class="contact-bar">
    <div class="contact-tab"></div>
    <p class="contact-label">CALL <span class="soft">OR</span> TEXT</p>
    <p class="contact-details">858·471·6093 • ClearBayRestore.com</p>
  </footer>

</main>
</body>
</html>
```